Business card for law firm

Need business card for new law firm. Think confident, authoritative, conservative, but not stuffy or old-fashioned.

Contact Information for Business Card

Content for card - logo (uploaded), plus the following:

Paul Whitcombe (larger font)
Managing Partner (larger font, but not as large as name)
Level 9, 7 Ferris Lane
Sydney NSW 2000
Main Tel 02 9364 2710
Direct Tel 02 8472 3159
Email paul@qvlegal.com.au
www.qvlegal.com.au

Letterhead design should include logo plus:
Level 9, 7 Ferris Lane
Sydney NSW 2000
Tel 02 8472 3159
www.qvlegal.com.au

```html
<!DOCTYPE html>
<html lang="en">
<head>
<meta charset="utf-8">
<title>Quayvale Lawyers – Business Card</title>
<link href="https://fonts.googleapis.com/css2?family=Cinzel:wght@400&family=Open+Sans:wght@400;700&display=swap" rel="stylesheet">
<style>
  :root {
    --navy: #001c54;
    --ink: #0a0a0a;
    --paper: #ffffff;
    --text: #1c1c1c;
    --bg-light: #ececee;
    --bg-dark: #c8c9cc;
  }
  html, body {
    margin: 0;
    width: 1200px;
    height: 1113px;
    overflow: hidden;
  }
  body {
    position: relative;
    background: linear-gradient(160deg, var(--bg-light) 0%, var(--bg-dark) 100%);
    font-family: "Open Sans", Arial, sans-serif;
  }
  .card {
    position: absolute;
    width: 773px;
    height: 442px;
    overflow: hidden;
  }
  .card--front {
    left: 75px; top: 79px;
    background: var(--paper);
    border-radius: 20px;
    border: 1px solid #9a9a9a;
    box-sizing: border-box;
  }
  .card--back {
    left: 367px; top: 589px;
    width: 773px; height: 441px;
    background: var(--ink);
    border-radius: 40px;
  }
  .front-swoosh { position: absolute; inset: 0; }
  .holder {
    position: absolute;
    right: 40px; top: 18px;
    text-align: right;
    color: var(--paper);
  }
  .holder__name { font-weight: 700; font-size: 27px; line-height: 36px; letter-spacing: 0.2px; }
  .holder__role { font-size: 19px; line-height: 28px; letter-spacing: 0.3px; }
  .brand-mark {
    position: absolute;
    background: var(--navy);
  }
  .card--front .brand-mark { left: 174px; top: 116px; width: 72px; height: 72px; }
  .card--back .brand-mark { left: 345px; top: 80px; width: 88px; height: 88px; background: var(--paper); }
  .firm {
    position: absolute;
    font-family: "Cinzel", Georgia, serif;
    font-weight: 400;
    text-align: center;
    line-height: 1;
  }
  .card--front .firm { left: 46px; top: 238px; width: 320px; color: var(--ink); }
  .card--front .firm__name { font-size: 50px; letter-spacing: 0.5px; }
  .card--front .firm__kind { font-size: 19px; letter-spacing: 20px; margin-top: 10px; padding-left: 20px; }
  .card--back .firm { left: 0; right: 0; top: 232px; color: var(--paper); }
  .card--back .firm__name { font-size: 60px; letter-spacing: 1px; }
  .card--back .firm__kind { font-size: 23px; letter-spacing: 29px; margin-top: 12px; padding-left: 29px; }
  .address {
    position: absolute;
    left: 43px; top: 362px;
    font-size: 20px; line-height: 31px;
    color: var(--text);
  }
  .contacts {
    position: absolute;
    right: 39px; top: 288px;
    list-style: none; margin: 0; padding: 0;
    font-size: 20px; line-height: 34.5px;
    color: var(--text);
    text-align: right;
  }
  .contacts li { display: flex; justify-content: flex-end; align-items: center; gap: 6px; }
  .contacts svg { width: 18px; height: 18px; flex: none; }
  .back-url {
    position: absolute;
    left: 0; right: 0; top: 370px;
    text-align: center;
    color: var(--paper);
    font-size: 24px;
    letter-spacing: 4.5px;
  }
  .back-url b { font-weight: 700; }
</style>
</head>
<body>

<section class="card card--front">
  <svg class="front-swoosh" viewBox="0 0 773 442" preserveAspectRatio="none" aria-hidden="true">
    <path fill="var(--ink)" d="M0,104 C130,68 300,50 460,72 C600,95 700,145 773,228 V186 C640,112 430,44 200,54 C120,58 50,72 0,86 Z"/>
    <path fill="var(--navy)" d="M0,0 H773 V186 C640,112 430,44 200,54 C120,58 50,72 0,86 Z"/>
    <path fill="none" stroke="var(--paper)" stroke-width="4" d="M0,97 C120,68 270,60 392,80"/>
  </svg>

  <div class="holder">
    <div class="holder__name">PAUL WHITCOMBE</div>
    <div class="holder__role">MANAGING PARTNER</div>
  </div>

  <div class="brand-mark"></div>
  <div class="firm">
    <div class="firm__name">QUAYVALE</div>
    <div class="firm__kind">LAWYERS</div>
  </div>

  <div class="address">Level 9, 7 Ferris Lane<br>Sydney NSW 2000</div>

  <ul class="contacts">
    <li>
      <svg viewBox="0 0 20 20" aria-hidden="true"><circle cx="10" cy="10" r="8.5" fill="none" stroke="var(--navy)" stroke-width="2"/><path d="M7 5 L9 7.5 L8 9 C8.6 10.6 9.6 11.6 11 12 L12.5 11 L15 13 L13.5 15 C9.5 15 5 10.5 5 6.5 Z" fill="var(--navy)"/></svg>
      <span>02 9364 2710(Main)</span>
    </li>
    <li>
      <svg viewBox="0 0 20 20" aria-hidden="true"><circle cx="10" cy="10" r="8.5" fill="none" stroke="var(--navy)" stroke-width="2"/><path d="M7 5 L9 7.5 L8 9 C8.6 10.6 9.6 11.6 11 12 L12.5 11 L15 13 L13.5 15 C9.5 15 5 10.5 5 6.5 Z" fill="var(--navy)"/></svg>
      <span>02 8472 3159(Direct)</span>
    </li>
    <li>
      <svg viewBox="0 0 20 20" aria-hidden="true"><path d="M2 8 L10 3 L18 8 V17 H2 Z" fill="var(--navy)"/><path d="M2 8 L10 13 L18 8" fill="none" stroke="var(--paper)" stroke-width="1.5"/></svg>
      <span>paul@qvlegal.com.au</span>
    </li>
    <li>
      <svg viewBox="0 0 20 20" aria-hidden="true" fill="none" stroke="var(--navy)" stroke-width="1.5"><circle cx="10" cy="10" r="8"/><ellipse cx="10" cy="10" rx="3.5" ry="8"/><path d="M2 10 H18 M3.5 6 H16.5 M3.5 14 H16.5"/></svg>
      <span>www.qvlegal.com.au</span>
    </li>
  </ul>
</section>

<section class="card card--back">
  <div class="brand-mark"></div>
  <div class="firm">
    <div class="firm__name">QUAYVALE</div>
    <div class="firm__kind">LAWYERS</div>
  </div>
  <div class="back-url">www.<b>qvlegal</b>.com.au</div>
</section>

</body>
</html>
```